VELORA Brisbane Tiling Service

My name is Milos Brendt i need a business card for a new company. We are wall and floor tilers based in Brisbane, our company is Velorix Brisbane Tiling Service.
We would like a logo from our website used on our cards. Our website is www.velorix.com.au

I would like my Chatterbook and Postwave accounts on my card.

Industry/Entity Type

Business

Colors
0692cd
3176b5
33a6d7
85cae6

```html
<!DOCTYPE html>
<html lang="en">
<head>
<meta charset="utf-8">
<title>Velorix Brisbane Tiling Service – Business Card</title>
<link rel="stylesheet" href="https://fonts.googleapis.com/css2?family=Arimo:wght@400&display=swap">
<style>
  :root {
    --brand-blue: #0a74b8;
    --brand-blue-deep: #0669a8;
    --brand-sky: #33a6d7;
    --card-white: #ffffff;
    --tile-grey: #ececec;
    --stage: #e4e6e6;
    --ink-white: #f4f8fb;
  }
  * { margin: 0; padding: 0; box-sizing: border-box; }
  html, body { width: 1200px; height: 900px; overflow: hidden; }
  body {
    background: var(--stage);
    font-family: "Arimo", Arial, sans-serif;
    position: relative;
  }
  .card {
    position: absolute;
    left: 320px;
    width: 560px;
    height: 320px;
    background: var(--card-white);
    box-shadow: 0 6px 18px rgba(0,0,0,0.25);
    overflow: hidden;
  }
  .card--front { top: 95px; }
  .card--back  { top: 485px; }

  .tile-field {
    position: absolute;
    inset: 0;
    background: linear-gradient(160deg, #ffffff 0%, var(--tile-grey) 55%, #f6f6f6 100%);
  }

  /* Front: wordmark */
  .wordmark {
    position: absolute;
    left: 50%;
    top: 50%;
    transform: translate(-50%, -50%);
    display: flex;
    align-items: center;
    gap: 10px;
    color: var(--brand-blue);
  }
  .wordmark__square {
    width: 52px; height: 52px;
    background: var(--brand-blue);
    border-radius: 3px;
  }
  .wordmark__name { font-size: 42px; line-height: 1; letter-spacing: 0.5px; }
  .wordmark__tagline { font-size: 15px; margin-top: 4px; }

  /* Back */
  .back__emblem {
    position: absolute;
    left: 50%;
    top: 42px;
    transform: translateX(-50%);
    width: 150px; height: 100px;
    background: var(--brand-blue);
    border-radius: 8px;
  }
  .back__band {
    position: absolute;
    left: 0; right: 0; bottom: 0;
    height: 132px;
    background: linear-gradient(180deg, var(--brand-blue) 0%, var(--brand-blue-deep) 100%);
  }
  .holder {
    position: absolute;
    left: 28px;
    bottom: 44px;
    display: flex;
    align-items: center;
    gap: 14px;
    color: var(--ink-white);
  }
  .holder__square { width: 44px; height: 44px; background: #eeeeee; }
  .holder__name { font-size: 26px; }

  .contacts {
    position: absolute;
    right: 24px;
    top: 10px;
    list-style: none;
    color: var(--ink-white);
    font-size: 10.5px;
  }
  .contacts li {
    display: flex;
    align-items: center;
    gap: 7px;
    height: 17px;
  }
  .contacts svg { width: 11px; height: 11px; flex: none; }
</style>
</head>
<body>

  <section class="card card--front" aria-label="Card front">
    <div class="tile-field" role="img" aria-label="Soft grey tile pattern background"></div>
    <div class="wordmark">
      <div class="wordmark__square"></div>
      <div>
        <div class="wordmark__name">velorix</div>
        <div class="wordmark__tagline">brisbane tiling service</div>
      </div>
    </div>
  </section>

  <section class="card card--back" aria-label="Card back">
    <div class="tile-field" role="img" aria-label="Soft grey tile pattern background"></div>
    <div class="back__emblem"></div>
    <div class="back__band">
      <ul class="contacts">
        <li>
          <svg viewBox="0 0 12 12"><rect width="12" height="12" rx="1.5" fill="#f4f8fb"/><path d="M3.5 2.5l1.5 0 .6 2-1 .8a5 5 0 0 0 2.1 2.1l.8-1 2 .6v1.5c-3.5.4-6.4-2.5-6-6z" fill="#0a74b8"/></svg>
          0400 555 219
        </li>
        <li>
          <svg viewBox="0 0 12 12"><rect width="12" height="12" rx="1.5" fill="#f4f8fb"/><rect x="2.5" y="3.5" width="7" height="5" fill="none" stroke="#0a74b8"/><path d="M2.5 3.5l3.5 3 3.5-3" fill="none" stroke="#0a74b8"/></svg>
          info@velorix.com.au
        </li>
        <li>
          <svg viewBox="0 0 12 12"><rect width="12" height="12" rx="1.5" fill="#f4f8fb"/><circle cx="6" cy="6" r="3.5" fill="none" stroke="#0a74b8"/><path d="M2.5 6h7M6 2.5v7" stroke="#0a74b8"/></svg>
          www.velorix.com.au
        </li>
        <li>
          <svg viewBox="0 0 12 12"><rect width="12" height="12" rx="1.5" fill="#f4f8fb"/></svg>
          /Velorix-Brisbane-Tiling-Service
        </li>
        <li>
          <svg viewBox="0 0 12 12"><rect width="12" height="12" rx="1.5" fill="#f4f8fb"/></svg>
          /infovelorix
        </li>
      </ul>
      <div class="holder">
        <div class="holder__square"></div>
        <div class="holder__name">Milos Brendt</div>
      </div>
    </div>
  </section>

</body>
</html>
```